R7M Horizon Business Card Design

We need a business card created for our New Business "R7M Horizon"<br/><br/>The business card design is up to you however the following information must be on the business card:<br/><br/>Front of the business card -<br/>Email :darrenp@r7mhorizon.nz<br/>Mobile: +64 (0) 22 4870 619<br/>Website: www.r7mhorizon.nz<br/>Card Owner Name: Darren Paltrow<br/>Company Title: Business Development Manager<br/>Slogan: "The BEST of both worlds". <br/>Logo On the front attached to the design brief<br/><br/>On the back: <br/>Space on the back for 4 more versions of the logo across the bottom of the card indicating different subsidiary brands - R7M Coffee, R7M Arts, R7M ?? (The card will be used for all of these brands - We Will add the extra subsidiary logos to the design once the design is finished (We are a graphics design team). <br/><br/>Other than that we want a premium feeling logo that remains universally usable depending on the business entity that we are using the card for. The use of bright bold colours would be great but we still want the card to feel premium.
Target Market(s)
Gift Design and Manufacturing Companies
Contact Information for Business Card
Front of the business card -
Email :darrenp@r7mhorizon.nz
Mobile: +64 (0) 22 4870 619
Website: www.r7mhorizon.nz
Card Owner Name: Darren Paltrow
Company Title: Business Development Manager
Slogan: "The BEST of both worlds".
Logo On the front attached to the design brief

```html
<!DOCTYPE html>
<html lang="en">
<head>
<meta charset="utf-8">
<title>R7M Horizon Business Card</title>
<link rel="stylesheet" href="https://fonts.googleapis.com/css2?family=Exo+2:ital,wght@0,400;0,500;0,600;1,400;1,700&display=swap">
<style>
  :root {
    --page-bg: #141414;
    --card-bg: #1f2021;
    --brand-blue: #3a4cb4;
    --mark-faint: #2c2e31;
    --text-light: #f2f2f2;
  }
  * { box-sizing: border-box; margin: 0; padding: 0; }
  html, body {
    width: 1200px; height: 900px; overflow: hidden;
    background: var(--page-bg);
    font-family: "Exo 2", Arial, sans-serif;
  }
  .card {
    position: absolute;
    left: 230px;
    width: 740px; height: 423px;
    background: var(--card-bg);
    border-left: 3px solid var(--brand-blue);
    border-bottom: 3px solid var(--brand-blue);
    overflow: hidden;
  }
  .card--back { top: 20px; }
  .card--front { top: 457px; }

  /* back */
  .back-name {
    position: absolute; left: 0; right: 0; top: 50%;
    transform: translateY(-50%);
    text-align: center;
    font-size: 44px; font-weight: 600;
    color: var(--mark-faint);
    letter-spacing: 1px;
  }

  /* front */
  .brand {
    position: absolute; left: 0; right: 0; top: 78px;
    text-align: center;
  }
  .brand-name {
    font-size: 52px; font-weight: 600;
    color: var(--brand-blue);
    line-height: 1;
  }
  .slogan {
    position: absolute; left: 0; right: 0; top: 168px;
    text-align: center;
    font-size: 22px; font-weight: 400;
    color: var(--brand-blue);
  }
  .divider {
    position: absolute; left: 70px; right: 60px; top: 212px;
    height: 2px; background: var(--brand-blue);
  }
  .holder {
    position: absolute; left: 70px; top: 232px;
  }
  .holder-name {
    font-size: 30px; font-weight: 700; font-style: italic;
    text-transform: uppercase;
    color: var(--brand-blue);
    line-height: 1.1;
  }
  .holder-title {
    font-size: 19px; font-style: italic;
    color: var(--text-light);
  }
  .contact {
    position: absolute; right: 50px; top: 294px;
    list-style: none;
  }
  .contact-item {
    display: flex; align-items: center; justify-content: flex-end; gap: 14px;
    font-size: 21px; font-weight: 500;
    color: var(--text-light);
    height: 34px;
  }
  .contact-icon { width: 22px; height: 22px; flex: none; }
</style>
</head>
<body>
  <section class="card card--back" aria-label="Card back">
    <div class="back-name">R7M Horizon</div>
  </section>

  <section class="card card--front" aria-label="Card front">
    <div class="brand">
      <span class="brand-name">R7M Horizon</span>
    </div>
    <p class="slogan">The BEST of both worlds</p>
    <div class="divider"></div>

    <div class="holder">
      <p class="holder-name">Darren Paltrow</p>
      <p class="holder-title">Business Development Manager</p>
    </div>

    <ul class="contact">
      <li class="contact-item">+64 (0) 22 4870 619
        <svg class="contact-icon" viewBox="0 0 24 24" fill="none" stroke="#3a4cb4" stroke-width="1.8">
          <path d="M6.5 3.5c-1.6 1.2-1.8 4 .8 7.8s6 6.6 9.2 5.4l1.5-1.4-3-3-1.6 1c-1.6-.8-3.2-2.4-4-4l1-1.6-3-3z"/>
        </svg>
      </li>
      <li class="contact-item">darrenp@r7mhorizon.nz
        <svg class="contact-icon" viewBox="0 0 24 24" fill="none" stroke="#3a4cb4" stroke-width="1.8">
          <rect x="2" y="5" width="20" height="14" rx="1"/>
          <path d="M2 6l10 7 10-7"/>
        </svg>
      </li>
      <li class="contact-item">www.r7mhorizon.nz
        <svg class="contact-icon" viewBox="0 0 24 24" fill="none" stroke="#3a4cb4" stroke-width="1.8">
          <circle cx="12" cy="12" r="10"/>
          <ellipse cx="12" cy="12" rx="4.5" ry="10"/>
          <path d="M2 12h20M4 7h16M4 17h16"/>
        </svg>
      </li>
    </ul>
  </section>
</body>
</html>
```